Mobile Friendly Lead Generation Landing Page

We are a web marketing company that specialized in web lead generation. Recently we have started buying media from mobile devices and we need a mobile interface(landing page) where we can collect user data in an effective manner.

Our current mobile landing page is:
http://www.tutorpath.example.com/lp13d/index.aspx?a=true&source=841356
Through this you can see what the steps/questions users need to answer to get matched to a school. We need the design for the whole process.

We are pretty open for design ideas and our goal is to make this mobile optimized landing page have the look and feel of an app...but not an app.
There are several questions in the process but we are open to changing the way they are presented. As in, you can have one question at a time or a few.
The goal is to make this EXTREMELY EASY for users to interact with.

One example that we have liked is:
http://learnvane.example/schools/57214-page1.lvne (please note that this opens only on mobile devices)

Some of these screenshots are attached.

Our web form looks like this:
http://www.tutorpath.example.com/lp88/index.aspx?a=true

```html
<!DOCTYPE html>
<html lang="en">
<head>
<meta charset="utf-8">
<title>Main Screen - Revision 6.0</title>
<link rel="stylesheet" href="https://fonts.googleapis.com/css2?family=Roboto:wght@300;400;500&display=swap">
<style>
  :root {
    --bg-top: #eef7dc;
    --bg-bottom: #dcebf5;
    --title-band: rgba(255,255,255,0.75);
    --ink: #2b2b2b;
    --muted: #444;
    --screen: #ffffff;
    --chrome: #f4f4f6;
    --url-field: #dcdcdf;
    --divider: #d6d6d9;
    --brand-blue: #2a7ff0;
    --brand-red: #ee2020;
    --icon-blue: #2a7ff0;
    --chevron: #8e8e93;
    --nav-blue: #2a7ff0;
    --nav-disabled: #b9b9bf;
  }
  * { box-sizing: border-box; margin: 0; padding: 0; }
  html, body { width: 800px; height: 1200px; overflow: hidden; }
  body {
    font-family: "Roboto", Helvetica, Arial, sans-serif;
    background: linear-gradient(160deg, var(--bg-top) 0%, #f1f5e0 45%, var(--bg-bottom) 100%);
    color: var(--ink);
    position: relative;
  }
  .page-title {
    position: absolute; top: 20px; left: 0; width: 800px; height: 82px;
    background: var(--title-band);
    display: flex; align-items: center; justify-content: center;
    font-size: 44px; font-weight: 400; letter-spacing: 0.5px; color: var(--ink);
  }
  .screen {
    position: absolute; top: 142px; left: 107px; width: 586px;
    background: var(--screen);
    border: 7px solid #1d1d1f; border-radius: 10px;
    overflow: hidden;
  }
  .status-bar {
    height: 30px; background: var(--chrome);
    display: flex; align-items: center; justify-content: space-between;
    padding: 0 14px; font-size: 17px; font-weight: 500; color: #111;
  }
  .status-bar .carrier { display: flex; align-items: center; gap: 8px; }
  .status-bar .battery { display: flex; align-items: center; gap: 6px; }
  .address-area { background: var(--chrome); padding: 4px 12px 12px; }
  .address-field {
    height: 50px; background: var(--url-field); border-radius: 8px;
    display: flex; align-items: center; justify-content: center; position: relative;
    font-size: 26px; font-weight: 400; color: #222;
  }
  .address-field svg { position: absolute; right: 14px; }
  .spacer-strip { height: 24px; background: linear-gradient(90deg, #f3d2d2, #e4d9c8 40%, #d8e4da 70%, #dcecde); }
  .spacer-strip.tall { height: 36px; background: linear-gradient(90deg, #cfdcf2, #e8e6d6 45%, #f6e6c8 80%, #eee6d0); }
  .apply-band {
    height: 80px; background: var(--brand-blue); color: #fff;
    display: flex; align-items: center; justify-content: center;
    font-size: 25px; font-weight: 400; letter-spacing: 0.3px;
  }
  .grant-note {
    height: 86px; display: flex; align-items: center; justify-content: center;
    font-size: 22px; color: var(--muted); background: #fff;
  }
  .interest-band {
    height: 78px; background: var(--brand-red); color: #fff;
    display: flex; align-items: center; justify-content: center;
    font-size: 25px; letter-spacing: 0.3px;
  }
  .interest-list { list-style: none; }
  .interest-item {
    height: 79px; display: flex; align-items: center; padding: 0 22px;
    border-bottom: 1px solid var(--divider); font-size: 23px; color: #333;
  }
  .interest-item:last-child { border-bottom: none; }
  .interest-item .icon { width: 40px; height: 40px; margin-right: 22px; flex: none; }
  .interest-item .label { flex: 1; }
  .abc-icon { color: var(--icon-blue); font-size: 15px; line-height: 17px; text-align: center; }
  .abc-icon span { display: block; }
  .abc-icon span:first-child { border-bottom: 1.5px solid var(--icon-blue); }
  .toolbar {
    height: 90px; background: var(--chrome); border-top: 1px solid var(--divider);
    display: flex; align-items: center; justify-content: space-around;
  }
</style>
</head>
<body>
  <header class="page-title">Main Screen - Revision 6.0</header>

  <main class="screen">
    <div class="status-bar">
      <span class="carrier">
        <svg width="58" height="10" viewBox="0 0 58 10"><g fill="#111"><circle cx="5" cy="5" r="4.5"/><circle cx="16" cy="5" r="4.5"/><circle cx="27" cy="5" r="4.5"/></g><g fill="none" stroke="#111" stroke-width="1"><circle cx="38" cy="5" r="4"/><circle cx="49" cy="5" r="4"/></g></svg>
        Northwave
        <svg width="20" height="15" viewBox="0 0 20 15" fill="none" stroke="#111" stroke-width="2"><path d="M2 6a11 11 0 0 1 16 0"/><path d="M5 9a7 7 0 0 1 10 0"/><circle cx="10" cy="12.5" r="1.5" fill="#111" stroke="none"/></svg>
      </span>
      <span class="clock">4:21 PM</span>
      <span class="battery">100%
        <svg width="40" height="16" viewBox="0 0 40 16"><rect x="1" y="1" width="34" height="14" rx="3" fill="#111"/><rect x="36" y="5" width="3" height="6" rx="1" fill="#111"/></svg>
      </span>
    </div>
    <div class="address-area">
      <div class="address-field">tutorpath.example.com
        <svg width="24" height="24" viewBox="0 0 24 24" fill="none" stroke="#222" stroke-width="2.2"><path d="M19 12a7 7 0 1 1-3-5.7"/><path d="M13 5h4V1" /></svg>
      </div>
    </div>

    <div class="spacer-strip"></div>
    <div class="apply-band">COMPLETE OUR 3-MINUTE APP</div>
    <p class="grant-note">Get up to $5, 645* per year in Grants if you qualify</p>
    <div class="spacer-strip"></div>
    <div class="interest-band">SELECT AREA OF YOUR INTEREST</div>

    <ul class="interest-list">
      <li class="interest-item">
        <svg class="icon" viewBox="0 0 40 40" fill="none" stroke="var(--icon-blue)" stroke-width="1.8"><path d="M30 4 16 24"/><path d="M36 8 18 26"/><path d="M14 25c-5 0-6 5-7 10 5-1 11-2 11-7z"/></svg>
        <span class="label">Art &amp; Design</span>
        <svg width="14" height="22" viewBox="0 0 14 22" fill="none" stroke="var(--chevron)" stroke-width="2.5"><path d="M2 2l9 9-9 9"/></svg>
      </li>
      <li class="interest-item">
        <svg class="icon" viewBox="0 0 40 40" fill="none" stroke="var(--icon-blue)" stroke-width="1.8"><rect x="3" y="11" width="34" height="24" rx="2"/><path d="M14 11V6h12v5"/><path d="M3 22h34"/><rect x="17" y="19" width="6" height="6"/></svg>
        <span class="label">Business</span>
        <svg width="14" height="22" viewBox="0 0 14 22" fill="none" stroke="var(--chevron)" stroke-width="2.5"><path d="M2 2l9 9-9 9"/></svg>
      </li>
      <li class="interest-item">
        <svg class="icon" viewBox="0 0 40 40" fill="none" stroke="var(--icon-blue)" stroke-width="1.8"><rect x="12" y="4" width="12" height="9" transform="rotate(40 18 8)"/><path d="M17 14 5 27"/><path d="M9 35h18" stroke-width="3"/></svg>
        <span class="label">Criminal Justice</span>
        <svg width="14" height="22" viewBox="0 0 14 22" fill="none" stroke="var(--chevron)" stroke-width="2.5"><path d="M2 2l9 9-9 9"/></svg>
      </li>
      <li class="interest-item">
        <div class="icon abc-icon"><span>ABC</span><span>1 2 3</span></div>
        <span class="label">Education &amp; Teaching</span>
        <svg width="14" height="22" viewBox="0 0 14 22" fill="none" stroke="var(--chevron)" stroke-width="2.5"><path d="M2 2l9 9-9 9"/></svg>
      </li>
      <li class="interest-item">
        <svg class="icon" viewBox="0 0 40 40" fill="none" stroke="var(--icon-blue)" stroke-width="1.8"><circle cx="20" cy="7" r="3"/><path d="M18 10 7 36"/><path d="M22 10l11 26"/><path d="M8 26c8 4 16 4 24 0"/></svg>
        <span class="label">Engineering</span>
        <svg width="14" height="22" viewBox="0 0 14 22" fill="none" stroke="var(--chevron)" stroke-width="2.5"><path d="M2 2l9 9-9 9"/></svg>
      </li>
      <li class="interest-item">
        <svg class="icon" viewBox="0 0 40 40" fill="none" stroke="var(--icon-blue)" stroke-width="1.8"><path d="M3 10c6-2 12-2 17 2 5-4 11-4 17-2v20c-6-2-12-2-17 2-5-4-11-4-17-2z"/><path d="M20 12v20"/></svg>
        <span class="label">Other</span>
        <svg width="14" height="22" viewBox="0 0 14 22" fill="none" stroke="var(--chevron)" stroke-width="2.5"><path d="M2 2l9 9-9 9"/></svg>
      </li>
    </ul>

    <div class="spacer-strip tall"></div>

    <nav class="toolbar">
      <svg width="20" height="34" viewBox="0 0 20 34" fill="none" stroke="var(--nav-blue)" stroke-width="2.5"><path d="M17 3 3 17l14 14"/></svg>
      <svg width="20" height="34" viewBox="0 0 20 34" fill="none" stroke="var(--nav-disabled)" stroke-width="2.5"><path d="M3 3l14 14L3 31"/></svg>
      <svg width="30" height="40" viewBox="0 0 30 40" fill="none" stroke="var(--nav-blue)" stroke-width="2.2"><path d="M10 14H3v24h24V14h-7"/><path d="M15 26V2"/><path d="M8 9l7-7 7 7"/></svg>
      <svg width="36" height="30" viewBox="0 0 36 30" fill="none" stroke="var(--nav-blue)" stroke-width="2.2"><path d="M2 3c6-1 12 0 16 3 4-3 10-4 16-3v23c-6-1-12 0-16 3-4-3-10-4-16-3z"/><path d="M18 6v23"/></svg>
      <svg width="34" height="34" viewBox="0 0 34 34" fill="none" stroke="var(--nav-blue)" stroke-width="2.2"><rect x="2" y="10" width="22" height="22"/><path d="M10 10V2h22v22h-8"/></svg>
    </nav>
  </main>
</body>
</html>
```